Estate Agent Board Design

Most eye-catching, elegant estate agent board
Company logo should stand out
Korvimark & TREG should be small but visible.

On the board must be:

"FOR SALE"
logos
website zhbproperties.co.uk
tel number 01632 960418

It Company

```html
<!DOCTYPE html>
<html lang="en">
<head>
<meta charset="utf-8">
<title>zhb Sales &amp; Lettings – For Sale Board</title>
<link rel="stylesheet" href="https://fonts.googleapis.com/css2?family=Montserrat:wght@400;600;700;800;900&display=swap">
<style>
  :root {
    --page-bg: #e8ebe8;
    --frame: #8e9294;
    --board-white: #ffffff;
    --board-tint: #eeeeea;
    --green-dark: #1a4a1d;
    --green-bright: #1f8d38;
    --ink: #2a2a2a;
    --badge-navy: #1d3f8a;
    --badge-blue: #2f6fc0;
  }
  * { margin: 0; padding: 0; box-sizing: border-box; }
  html, body {
    width: 1200px; height: 798px; overflow: hidden;
    background: var(--page-bg);
    font-family: "Montserrat", sans-serif;
  }
  .board {
    position: absolute;
    left: 317px; top: 29px;
    width: 566px; height: 740px;
    border: 8px solid var(--frame);
    background: radial-gradient(ellipse at 40% 35%, var(--board-white) 0%, var(--board-tint) 100%);
    overflow: hidden;
  }
  .brand { position: absolute; left: 54px; top: 78px; }
  .brand-mark {
    position: absolute; left: 0; top: 0;
    width: 168px; height: 168px;
    background: var(--green-dark);
  }
  .brand-name {
    position: absolute; left: 180px; top: -22px;
    font-weight: 900; font-size: 150px; line-height: 1;
    letter-spacing: -6px;
    color: var(--green-dark);
  }
  .brand-tagline {
    position: absolute; left: 183px; top: 141px;
    font-weight: 700; font-size: 24px; white-space: nowrap;
    color: var(--green-dark);
  }
  .headline {
    position: absolute; left: 0; right: 0; top: 350px;
    text-align: center;
    font-weight: 900; font-size: 80px; letter-spacing: 3px;
    color: var(--green-dark);
  }
  .phone {
    position: absolute; left: 0; right: 0; top: 478px;
    display: flex; justify-content: center; align-items: center; gap: 10px;
    font-weight: 800; font-size: 46px; letter-spacing: 1px;
    color: var(--ink);
  }
  .phone svg { width: 36px; height: 40px; }
  .accreditations {
    position: absolute; left: 0; right: 0; top: 593px;
    display: flex; justify-content: center; gap: 14px;
  }
  .badge { width: 66px; height: 66px; }
  .badge--square { background: var(--badge-navy); border-radius: 10px; }
  .badge--round { background: var(--badge-blue); border-radius: 50%; }
  .web-band {
    position: absolute; left: 0; right: 0; bottom: 0; height: 52px;
  }
  .web-band svg { position: absolute; inset: 0; width: 100%; height: 100%; }
  .web-address {
    position: absolute; left: 22px; top: 0; height: 52px;
    display: flex; align-items: center;
    font-weight: 600; font-size: 21px; letter-spacing: 3px;
    color: #ffffff;
  }
</style>
</head>
<body>
  <div class="board">
    <div class="brand">
      <div class="brand-mark"></div>
      <div class="brand-name">zhb</div>
      <div class="brand-tagline">SALES &amp; LETTINGS</div>
    </div>

    <div class="headline">FOR SALE</div>

    <div class="phone">
      <svg viewBox="0 0 24 28" aria-hidden="true">
        <path d="M6 2 L10 2 L11.5 8 L8.5 10 C9.5 14 11 17 14 20 L17 18 L22 21 L21 25 C19 27 15 26.5 11 22 C6 17 3 11 3.5 6 C3.7 4 4.5 2.5 6 2 Z" fill="#1f8d38"/>
      </svg>
      <span>01632 960418</span>
    </div>

    <div class="accreditations">
      <div class="badge badge--square" role="img" aria-label="Korvimark accreditation"></div>
      <div class="badge badge--round" role="img" aria-label="TREG accreditation"></div>
    </div>

    <div class="web-band">
      <svg viewBox="0 0 550 52" preserveAspectRatio="none" aria-hidden="true">
        <rect x="0" y="0" width="550" height="52" fill="#1a4a1d"/>
        <polygon points="405,0 550,0 550,52 405,52 420,26" fill="#1f8d38"/>
        <polyline points="393,6 411,26 393,46" fill="none" stroke="#ffffff" stroke-width="5"/>
        <polyline points="409,6 427,26 409,46" fill="none" stroke="#1f8d38" stroke-width="5"/>
      </svg>
      <div class="web-address">www.zhbproperties.co.uk</div>
    </div>
  </div>
</body>
</html>
```